Coastline Premier Retreats Business Card Design

Design a business card for Coastline Premier Retreats. Look at the website for colors and reference. Card should have logo, name, title, office number, mobile number, email, URL and a tagline like, "Luxury Hotel & Resort Email Marketing" (This might change).

https://www.coastlinepremierretreats.example

The rest I will leave up to your imagination.

Contact Information for Business Card

Logo, name, title, office number, mobile number, email, URL and a tagline like, "Luxury Hotel & Resort Email Marketing" (This might change).

```html
<!DOCTYPE html>
<html lang="en">
<head>
<meta charset="utf-8">
<title>Coastline Premier Retreats – Business Card</title>
<link href="https://fonts.googleapis.com/css2?family=Open+Sans:wght@400;600;700&display=swap" rel="stylesheet">
<style>
  :root {
    --canvas: #232323;
    --card: #1f1f22;
    --card-back: #18181a;
    --orange: #f37421;
    --white: #ffffff;
    --muted: #e6e6e6;
    --emboss: #2a2a2e;
  }
  * { box-sizing: border-box; margin: 0; padding: 0; }
  html, body { width: 1200px; height: 780px; overflow: hidden; background: var(--canvas); }
  body { font-family: "Open Sans", Arial, sans-serif; color: var(--white); }

  .stage { position: relative; width: 1200px; height: 780px; }

  .card {
    position: absolute; top: 236px;
    width: 540px; height: 309px;
    background: var(--card);
    box-shadow: 0 18px 40px rgba(0,0,0,.55);
    overflow: hidden;
  }
  .card--front { left: 40px; }
  .card--back  { left: 620px; background: var(--card-back); }

  .card__shapes { position: absolute; inset: 0; width: 540px; height: 309px; }

  .brand {
    position: absolute; left: 232px; top: 38px;
    display: flex; align-items: center; gap: 8px;
    white-space: nowrap;
  }
  .brand__square { width: 12px; height: 12px; background: var(--orange); flex: none; }
  .brand__name {
    font-weight: 700; font-size: 16px; letter-spacing: .02em;
    color: var(--white); text-transform: uppercase;
  }

  .person { position: absolute; left: 40px; top: 78px; white-space: nowrap; }
  .person__name { font-size: 22px; font-weight: 700; line-height: 1.15; }
  .person__first { color: var(--orange); }
  .person__last { color: var(--white); }
  .person__title { margin-top: 4px; font-size: 12.5px; font-weight: 400; color: var(--muted); padding-left: 22px; }

  .divider { position: absolute; left: 226px; top: 118px; width: 1.5px; height: 80px; background: var(--white); }

  .contacts { position: absolute; left: 240px; top: 120px; list-style: none; }
  .contacts__item {
    display: flex; align-items: center; gap: 7px;
    font-size: 12px; line-height: 19px; color: var(--white); white-space: nowrap;
  }
  .contacts__icon { width: 11px; height: 11px; flex: none; }

  .tagline {
    position: absolute; left: 64px; top: 270px;
    font-size: 12.5px; font-weight: 400; color: var(--white); white-space: nowrap;
  }

  .back-brand {
    position: absolute; inset: 0;
    display: flex; align-items: center; justify-content: center; gap: 12px;
    white-space: nowrap;
  }
  .back-brand__square { width: 16px; height: 16px; background: var(--emboss); flex: none; }
  .back-brand__name {
    font-weight: 700; font-size: 22px; letter-spacing: .02em;
    text-transform: uppercase; color: var(--emboss);
  }
</style>
</head>
<body>
<main class="stage">

  <section class="card card--front" aria-label="Business card front">
    <svg class="card__shapes" viewBox="0 0 540 309" aria-hidden="true">
      <path d="M0,208 C120,266 330,300 540,238 L540,309 L0,309 Z" fill="var(--orange)"/>
      <path d="M70,204 C150,262 330,292 520,244" fill="none" stroke="var(--white)" stroke-width="3" stroke-linecap="round"/>
    </svg>

    <div class="brand">
      <span class="brand__square"></span>
      <span class="brand__name">Coastline Premier Retreats</span>
    </div>

    <div class="person">
      <p class="person__name"><span class="person__first">Marta</span> <span class="person__last">Kovalenko</span></p>
      <p class="person__title">Managing Director</p>
    </div>

    <div class="divider"></div>

    <ul class="contacts">
      <li class="contacts__item">
        <svg class="contacts__icon" viewBox="0 0 12 12"><path d="M2.5 1 L4.5 1 L5.2 3.5 L4 4.4 C4.6 5.8 5.9 7.2 7.4 7.9 L8.4 6.8 L11 7.6 L11 9.6 C11 10.4 10.3 11 9.5 11 C5 10.6 1.3 6.9 1 2.4 C1 1.6 1.6 1 2.5 1 Z" fill="var(--orange)"/></svg>
        (555) 014-3120
      </li>
      <li class="contacts__item">
        <svg class="contacts__icon" viewBox="0 0 12 12"><rect x="3" y="0.8" width="6" height="10.4" rx="1" fill="none" stroke="var(--orange)" stroke-width="1.2"/><circle cx="6" cy="9.4" r=".7" fill="var(--orange)"/></svg>
        (555) 014-6481
      </li>
      <li class="contacts__item">
        <svg class="contacts__icon" viewBox="0 0 12 12"><circle cx="6" cy="6" r="5" fill="none" stroke="var(--orange)" stroke-width="1.2"/><ellipse cx="6" cy="6" rx="2.2" ry="5" fill="none" stroke="var(--orange)" stroke-width="1"/><path d="M1 6 H11" stroke="var(--orange)" stroke-width="1"/></svg>
        www.coastlinepremierretreats.example
      </li>
      <li class="contacts__item">
        <svg class="contacts__icon" viewBox="0 0 12 12"><rect x="0.8" y="2.2" width="10.4" height="7.6" fill="var(--orange)"/><path d="M0.8 2.4 L6 6.6 L11.2 2.4" fill="none" stroke="var(--card)" stroke-width="1"/></svg>
        info@coastlinepremierretreats.example
      </li>
    </ul>

    <p class="tagline">Luxury Hotel &amp; Resort Email Marketing</p>
  </section>

  <section class="card card--back" aria-label="Business card back">
    <div class="back-brand">
      <span class="back-brand__square"></span>
      <span class="back-brand__name">Coastline Premier Retreats</span>
    </div>
  </section>

</main>
</body>
</html>
```